New Business Card Design Project LORVANTI-Italy

we are LORVANTI-Italy
our company in the market for 3 years we are luxury cosmetic company and its about time for a facelift :)
i will like to have elegant luxurious and unique business card
that will give the person that get it a unique, luxurious and elegant impression
I'm VERY OPEN FOR NEW IDEAS , even duo i add a few files of things that i see on line and i like them

i add my logo as well
my website is LORVANTI.COM
(if you would like to see the main style that we have)

Target Market(s)

adult that have money :)

Industry/Entity Type

Business

Contact Information for Business Card

Name - Dario Lorvanti
Position - CEO and CO Founder
address - 4817 E Halvern
telephone - 555-384-1926
email - dario@lorvanti.com
fax - 555-384-1926
website - LORVANTI.COM

Colors
000000
959595
fbee3e
ffffff

Requirements
Must have
• big logo in GOLD color
• elegant look
• impressive
Nice to have
• not must but maybe classy pattern background
• not must but maybe emblem
• maybe clear plastic business card
Should not have
• colors
• images

```html
<!DOCTYPE html>
<html lang="en">
<head>
<meta charset="utf-8">
<title>LORVANTI Business Card</title>
<link rel="stylesheet" href="https://fonts.googleapis.com/css2?family=Cormorant+Garamond:wght@600&family=Ubuntu:wght@400&display=swap">
<style>
  :root {
    --stage: #0d0d0d;
    --card: #1b1b1b;
    --card-deep: #121212;
    --gold: #d8b14a;
    --ornament: #3a3a3a;
    --serif: "Cormorant Garamond", "Times New Roman", serif;
    --sans: "Ubuntu", Arial, sans-serif;
  }
  * { box-sizing: border-box; margin: 0; padding: 0; }
  html, body { width: 1200px; height: 1200px; overflow: hidden; }
  body {
    background: var(--stage);
    display: flex;
    align-items: center;
    justify-content: center;
    gap: 60px;
  }
  .card {
    position: relative;
    width: 400px;
    height: 700px;
    background: linear-gradient(180deg, var(--card) 0%, var(--card-deep) 100%);
    overflow: hidden;
    box-shadow: 0 20px 50px rgba(0,0,0,.6);
  }
  .card__ornament {
    position: absolute;
    left: -60px;
    right: -60px;
    bottom: -330px;
    height: 620px;
    border-radius: 50%;
    background: radial-gradient(circle at 50% 50%, transparent 0 38%, var(--ornament) 39% 62%, transparent 63%);
    opacity: .7;
  }
  .brand {
    position: absolute;
    left: 0;
    right: 0;
    display: flex;
    flex-direction: column;
    align-items: center;
    color: var(--gold);
  }
  .brand__seal {
    border: 4px solid var(--gold);
    border-radius: 50%;
  }
  .brand__name {
    font-family: var(--serif);
    font-weight: 600;
    letter-spacing: 1px;
    line-height: 1;
  }
  .card--front .brand { top: 130px; }
  .card--front .brand__seal { width: 150px; height: 150px; margin-bottom: 40px; }
  .card--front .brand__name { font-size: 66px; }

  .card--back .brand { bottom: 70px; }
  .card--back .brand__seal { width: 96px; height: 96px; margin-bottom: 22px; border-width: 3px; }
  .card--back .brand__name { font-size: 44px; }

  .holder {
    position: absolute;
    top: 98px;
    left: 50px;
    color: var(--gold);
    font-family: var(--sans);
  }
  .holder__name { font-size: 30px; }
  .holder__role { font-size: 19px; margin-top: 6px; }

  .contacts {
    position: absolute;
    top: 212px;
    left: 56px;
    list-style: none;
    font-family: var(--sans);
    font-size: 14px;
    color: var(--gold);
  }
  .contacts li {
    display: flex;
    align-items: center;
    gap: 14px;
    height: 42px;
  }
  .contacts svg { width: 16px; height: 16px; fill: var(--gold); flex: none; }
</style>
</head>
<body>

  <section class="card card--front" aria-label="Card front">
    <div class="card__ornament" role="img" aria-label="Faint large ornamental emblem pattern"></div>
    <div class="brand">
      <div class="brand__seal"></div>
      <div class="brand__name">LORVANTI</div>
    </div>
  </section>

  <section class="card card--back" aria-label="Card back">
    <div class="card__ornament" role="img" aria-label="Faint large ornamental emblem pattern"></div>
    <div class="holder">
      <div class="holder__name">Dario Lorvanti</div>
      <div class="holder__role">CEO and CO Founder</div>
    </div>
    <ul class="contacts">
      <li>
        <svg viewBox="0 0 16 16"><path d="M8 0a5.5 5.5 0 0 0-5.5 5.5C2.5 10 8 16 8 16s5.5-6 5.5-10.5A5.5 5.5 0 0 0 8 0zm0 8a2.5 2.5 0 1 1 0-5 2.5 2.5 0 0 1 0 5z"/></svg>
        4817 E Halvern
      </li>
      <li>
        <svg viewBox="0 0 16 16"><path d="M3.6 1l2.6 3-1.5 1.7a10 10 0 0 0 5.6 5.6L12 9.8l3 2.6-1.6 2.4C7.3 14.6 1.4 8.7 1.2 2.6z"/></svg>
        555-384-1926
      </li>
      <li>
        <svg viewBox="0 0 16 16"><path d="M1 3h14v10H1zm1.5 1.5v.3L8 9l5.5-4.2v-.3z"/></svg>
        dario@lorvanti.com
      </li>
      <li>
        <svg viewBox="0 0 16 16"><path d="M4 1h7v4H4zM1 6h14v7h-3v2H4v-2H1zm4 5v3h6v-3z"/></svg>
        555-384-1926
      </li>
      <li>
        <svg viewBox="0 0 16 16"><path d="M8 1a7 7 0 1 0 0 14A7 7 0 0 0 8 1zm0 1.4c.8 0 1.8 1.6 2.1 4.1H5.9C6.2 4 7.2 2.4 8 2.4zM2.5 7.5h2.2c0 .4 0 .7.1 1H2.5zm.1 1.4h2.3c.1 1.4.5 2.7 1 3.6A5.6 5.6 0 0 1 2.6 8.9zM8 13.6c-.8 0-1.8-1.6-2.1-4.7h4.2c-.3 3.1-1.3 4.7-2.1 4.7zm2.1-1.1c.5-.9.9-2.2 1-3.6h2.3a5.6 5.6 0 0 1-3.3 3.6zm1.2-4h2.2c0-.3 0-.7-.1-1h-2.1z"/></svg>
        LORVANTI.COM
      </li>
    </ul>
    <div class="brand">
      <div class="brand__seal"></div>
      <div class="brand__name">LORVANTI</div>
    </div>
  </section>

</body>
</html>
```